Strategy and Technology Consulting - Our Story and Values Page

Interior Page design – Our History and Our Values

Our homepage has been designed and we are looking for a design for one of the interior pages. This interior page tells the story of Our History and Our Values

Because the homepage has been designed, we would like this interior page to reflect the design of the homepage without being a mirror image of the homepage.

This site will be implemented in WordPress using the Elementor framework.

Font: Poppins medium and Poppins dark
Illustrations: Our homepage illustrations were designed by “Brelin 1974” on Quillmark. Compatible original or stock illustrations are welcome. Stock photography is also welcome. Brelin is also available through Brelin Tosamek on Ravolo

Uploaded Files
• Homepage design – this is the design we will use for our homepage. Contest entries should reflect this basic style but should be distinctly different from the homepage.
• Our History and Our Values – Wireframe – the basic layout of the page we are looking for.
• Our History and Our Values – Word document with the text supporting the wireframe.
• Color Palette – please use colors compatible with the palette attached.

Our Story - timeline
There is a timeline element in the wireframe. The wireframe displays this as a series of chevrons (arrows), but it does not need to be. Creativity in display of the timeline is appreciated.

Our Values
If you look at the Word document, you will see that there are a lot of words on the page. The winning design will present the information in a way that engages the user without overwhelming them with too much to read. For example, they may click on a value and see more information.

Target Market(s)

CIO's and Technology Executives

Number of Pages Required

1 page

Font styles to use
Sans Serif
Other font styles liked:
• Poppin

Requirements
Must have
• A timeline element, all of our values
Nice to have
• Clever timeline display

```html
<!DOCTYPE html>
<html lang="en">
<head>
<meta charset="utf-8">
<title>Solvanta – Our History and Values</title>
<link href="https://fonts.googleapis.com/css2?family=Poppins:wght@400;500;600;700;800&family=Roboto:wght@400;500&display=swap" rel="stylesheet">
<style>
:root{
  --yellow:#f0b719;
  --yellow-dark:#e3a90e;
  --navy:#3d4d63;
  --navy-deep:#354459;
  --text:#3a3a3a;
  --muted:#666;
  --line:#e6e6e6;
  --white:#fff;
}
*{margin:0;padding:0;box-sizing:border-box}
html,body{width:1200px;height:2882px;overflow:hidden;background:var(--white)}
body{position:relative;font-family:"Roboto",sans-serif;color:var(--text)}
.abs{position:absolute}

/* header */
.site-header{position:absolute;left:0;top:0;width:1200px;height:93px;border-bottom:1px solid #eee}
.brand{position:absolute;left:92px;top:22px;display:flex;align-items:center;gap:8px;font-family:"Poppins",sans-serif;font-weight:500;font-size:44px;color:#a9a9a9;letter-spacing:1px}
.brand-mark{width:14px;height:14px;background:#3f6fb8}
.nav{position:absolute;left:542px;top:36px;display:flex;gap:22px;font-family:"Poppins",sans-serif;font-weight:600;font-size:13px;color:var(--navy)}
.nav span::after{content:" ⌄";font-size:11px}
.nav .home::after{content:""}
.btn{display:flex;align-items:center;justify-content:center;background:var(--yellow);color:#fff;font-family:"Poppins",sans-serif;font-weight:700;font-size:12px;border-radius:22px}
.header-btn{position:absolute;left:981px;top:27px;width:131px;height:39px}

/* headings */
.section-title{position:absolute;left:0;width:1200px;text-align:center;font-family:"Poppins",sans-serif;font-weight:800;font-size:45px;color:var(--navy)}

/* history */
.era{position:absolute;top:244px;width:320px;height:261px;background:#fff;border:1px solid #eee;box-shadow:0 8px 30px rgba(0,0,0,.08)}
.ribbon{position:absolute;left:30px;top:-26px;width:188px;height:52px}
.ribbon span{position:absolute;left:0;top:0;width:188px;height:52px;display:flex;align-items:center;justify-content:center;font-family:"Poppins",sans-serif;font-weight:600;font-size:16px;color:#fff}
.era ul{list-style:none;position:absolute;left:30px;top:53px;right:20px}
.era li{position:relative;padding-left:30px;font-size:15.5px;line-height:20px;color:#555;margin-bottom:20px}
.era li svg{position:absolute;left:0;top:3px}
.era li.sub{padding-left:64px;font-size:14.5px;margin-bottom:14px;margin-top:-4px}
.era li.sub svg{left:34px}

/* values */
.value{position:absolute;left:109px;width:980px;height:184px;background:#fff;border:1px solid #eee;box-shadow:0 10px 24px rgba(0,0,0,.07)}
.value-art{position:absolute;left:70px;top:40px;width:110px;height:105px;border-radius:10px;background:linear-gradient(135deg,#f7d46a,#f0b719);opacity:.55}
.value h3{position:absolute;left:234px;top:36px;font-family:"Poppins",sans-serif;font-weight:600;font-size:16px;color:var(--navy)}
.value p{position:absolute;left:234px;top:68px;width:700px;font-size:15.5px;line-height:26px;color:#3a3a3a}

/* newsletter & footer */
.footer-bg{position:absolute;left:0;top:2150px;width:1200px;height:732px}
.newsletter{position:absolute;left:136px;top:2168px;width:926px;height:207px;border-radius:104px;background:var(--yellow)}
.newsletter h2{position:absolute;left:82px;top:56px;font-family:"Poppins",sans-serif;font-weight:800;font-size:32px;color:#fff}
.newsletter p{position:absolute;left:82px;top:112px;width:420px;font-family:"Poppins",sans-serif;font-weight:500;font-size:15.5px;line-height:20px;color:#fff}
.email-field{position:absolute;left:550px;top:80px;width:321px;height:48px;background:#fff;border-radius:24px;display:flex;align-items:center;padding-left:24px;gap:10px;font-family:"Poppins",sans-serif;font-size:13px;color:#888}
.send{position:absolute;right:5px;top:5px;width:38px;height:38px;border-radius:50%;background:#9aa7b9;display:flex;align-items:center;justify-content:center}

.footer-brand{position:absolute;left:118px;top:2555px;display:flex;align-items:center;gap:10px;font-family:"Poppins",sans-serif;font-weight:500;font-size:66px;color:#d4d8de;letter-spacing:1px}
.footer-brand .brand-mark{width:18px;height:18px}
.socials{position:absolute;left:175px;top:2634px;display:flex;gap:8px}
.socials span{width:43px;height:43px;border-radius:50%;background:rgba(255,255,255,.22)}
.footer-btn{position:absolute;left:214px;top:2700px;width:131px;height:39px}
.col{position:absolute;top:2530px;font-family:"Poppins",sans-serif;color:#fff}
.col h4{font-weight:700;font-size:20px;margin-bottom:22px}
.col li{list-style:none;font-size:13px;color:#e3e6eb;margin-bottom:13px}
.col li::before{content:"› ";font-weight:600}
.contact-item{position:relative;padding-left:22px;font-size:13px;line-height:18px;color:#e3e6eb;margin-bottom:18px;width:180px}
.contact-item svg{position:absolute;left:0;top:2px}
.bottom-bar{position:absolute;left:0;top:2822px;width:1200px;height:60px;background:#3a4659;display:flex;align-items:center;justify-content:center;font-family:"Poppins",sans-serif;font-weight:500;font-size:13px;color:#fff}
.chat{position:absolute;left:1136px;top:2790px;width:48px;height:48px;border-radius:50%;background:var(--yellow);display:flex;align-items:center;justify-content:center}
</style>
</head>
<body>

<header class="site-header">
  <div class="brand"><span class="brand-mark"></span>Solvanta</div>
  <nav class="nav">
    <span class="home"><svg width="14" height="13" viewBox="0 0 14 13"><path d="M7 0 0 6h2v7h4V9h2v4h4V6h2z" fill="#8a97aa"/></svg></span>
    <span>ABOUT US</span><span>SERVICES</span><span>INSIGHTS</span><span>JOIN US</span>
  </nav>
  <div class="btn header-btn">CONTACT US</div>
</header>

<h1 class="section-title" style="top:118px">Our History</h1>

<svg width="0" height="0" style="position:absolute">
  <defs>
    <symbol id="tick" viewBox="0 0 14 14"><circle cx="7" cy="7" r="5.8" fill="none" stroke="#f0b719" stroke-width="1.6"/><path d="M4.3 7.2l2 1.9 3.5-3.7" fill="none" stroke="#f0b719" stroke-width="1.6"/></symbol>
    <symbol id="dot" viewBox="0 0 14 14"><circle cx="7" cy="7" r="5.6" fill="none" stroke="#3d4d63" stroke-width="1.5"/><circle cx="7" cy="7" r="2.4" fill="#3d4d63"/></symbol>
    <symbol id="chev" viewBox="0 0 188 52"><polygon points="0,0 160,0 188,26 160,52 0,52 28,26" fill="#f0b719"/><polygon points="0,0 28,26 0,52" fill="#e3a90e" opacity=".5"/></symbol>
  </defs>
</svg>

<section class="era" style="left:110px">
  <div class="ribbon"><svg width="188" height="52"><use href="#chev"/></svg><span>2017 – 2019</span></div>
  <ul>
    <li><svg width="14" height="14"><use href="#tick"/></svg>Growth Strategy Focus</li>
    <li><svg width="14" height="14"><use href="#tick"/></svg>Consistent, Modest Growth</li>
    <li><svg width="14" height="14"><use href="#tick"/></svg>Preliminary Focus on Technology</li>
    <li><svg width="14" height="14"><use href="#tick"/></svg>Eureka! Implementing strategy is hard</li>
  </ul>
</section>
<section class="era" style="left:441px">
  <div class="ribbon"><svg width="188" height="52"><use href="#chev"/></svg><span>2020 – 2021</span></div>
  <ul>
    <li><svg width="14" height="14"><use href="#tick"/></svg>Pandemic Pauses Growth</li>
    <li><svg width="14" height="14"><use href="#tick"/></svg>Rethinking</li>
    <li class="sub"><svg width="14" height="14"><use href="#dot"/></svg>The business model</li>
    <li class="sub"><svg width="14" height="14"><use href="#dot"/></svg>The delivery model</li>
  </ul>
</section>
<section class="era" style="left:771px">
  <div class="ribbon"><svg width="188" height="52"><use href="#chev"/></svg><span>2022 and Onward</span></div>
  <ul>
    <li><svg width="14" height="14"><use href="#tick"/></svg>Leadership Team for Focus on Essential Areas</li>
    <li><svg width="14" height="14"><use href="#tick"/></svg>Rapid Growth</li>
    <li><svg width="14" height="14"><use href="#tick"/></svg>Customer Success</li>
  </ul>
</section>

<h2 class="section-title" style="top:572px">Our Values</h2>

<article class="value" style="top:662px">
  <div class="value-art" role="img" aria-label="Line illustration of a hand holding a shining diamond"></div>
  <h3>The Value of Every&nbsp; Human. Regardless.</h3>
  <p>Each person's unique experiences and perspectives add vibrant hues to the tapestry of our shared existence.&nbsp; In a world where diversity paints the canvas of humanity, true beauty is found in recognizing the inherent and incalculable value of every human being.</p>
</article>
<article class="value" style="top:864px">
  <div class="value-art" role="img" aria-label="Line illustration of four hands joined together"></div>
  <h3>Collaboration</h3>
  <p>Collaboration in work transforms individual endeavors into symphonies of collective achievement. Through collaboration, diverse talents converge, fostering a rich exchange of ideas that amplifies creativity, accelerates progress, and brings forth solutions beyond what a single mind could conceive.</p>
</article>
<article class="value" style="top:1066px">
  <div class="value-art" role="img" aria-label="Line illustration of a raised fist with a check mark"></div>
  <h3>Passion</h3>
  <p>Passion infuses our work with energy, transforming routine tasks into opportunities for creativity and innovation. Fueled by passion, individuals become unstoppable forces, driven to overcome challenges and achieve remarkable outcomes that benefit them and inspire those around them</p>
</article>
<article class="value" style="top:1268px">
  <div class="value-art" role="img" aria-label="Line illustration of a hand holding an award badge"></div>
  <h3>Excellence</h3>
  <p>Excellence isn't a destination; it's a continuous journey of refinement and growth. Striving for excellence cultivates a culture of continuous improvement, fostering innovation, credibility, and a lasting impact that resonates far beyond the immediate task.</p>
</article>
<article class="value" style="top:1470px">
  <div class="value-art" role="img" aria-label="Line illustration of a determined worker at a desk"></div>
  <h3>Tenacity</h3>
  <p>Tenacity is the unwavering anchor that keeps us grounded amidst adversity, propelling us forward when faced with obstacles. The resilience to persist, adapt, and learn from setbacks leads to the mastery of skills and the fulfillment of ambitious goals.</p>
</article>
<article class="value" style="top:1672px">
  <div class="value-art" role="img" aria-label="Line illustration of a person with puzzle pieces and plus signs"></div>
  <h3>Solution Mindset</h3>
  <p>A solution mindset is the compass that directs our focus from problems to possibilities. It empowers us to navigate challenges with a proactive mindset, igniting a journey of exploration and innovation that not only resolves issues but also paves the way for continuous growth and success.</p>
</article>
<article class="value" style="top:1874px">
  <div class="value-art" role="img" aria-label="Line illustration of two hands around a heart"></div>
  <h3>Generosity</h3>
  <p>Generosity creates a virtuous cycle of goodwill, fostering a sense of unity and shared purpose among colleagues. By freely sharing knowledge, support, and resources, we uplift those around us and contribute to a collaborative environment where collective achievements flourish.</p>
</article>

<svg class="footer-bg" viewBox="0 0 1200 732" preserveAspectRatio="none">
  <defs>
    <linearGradient id="ftg" x1="0" y1="1" x2="1" y2="0">
      <stop offset="0" stop-color="#63738b"/><stop offset=".5" stop-color="#46566e"/><stop offset="1" stop-color="#3f4e65"/>
    </linearGradient>
  </defs>
  <path d="M0 45 C140 70 230 160 330 210 C430 260 520 240 610 200 C700 160 780 190 860 230 C960 280 1080 150 1200 80 L1200 732 L0 732 Z" fill="url(#ftg)"/>
  <path d="M290 190 C400 250 500 250 600 205 C700 165 780 205 880 250" fill="none" stroke="#d9dde3" stroke-width="10" opacity=".6"/>
</svg>

<section class="newsletter">
  <h2>Subscribe Our Newsletter</h2>
  <p>Subscribe our newsletter to receive the latest news and exclusive offers every week, No spam.</p>
  <div class="email-field">
    <svg width="14" height="11" viewBox="0 0 14 11"><rect width="14" height="11" rx="1" fill="#9aa7b9"/><path d="M0 1l7 5 7-5" fill="none" stroke="#fff" stroke-width="1.3"/></svg>
    Enter email address
    <span class="send"><svg width="14" height="14" viewBox="0 0 14 14"><path d="M1 7 13 1 9 13 7 8z" fill="#fff"/></svg></span>
  </div>
</section>

<div class="footer-brand"><span class="brand-mark"></span>Solvanta</div>
<div class="socials"><span></span><span></span><span></span><span></span></div>
<div class="btn footer-btn">CONTACT US</div>

<div class="col" style="left:491px">
  <h4>Quick links</h4>
  <ul><li>Home</li><li>About Us</li><li>Services</li><li>Insights</li><li>Join Us</li><li>Contact Us</li></ul>
</div>
<div class="col" style="left:668px">
  <h4>Our Services</h4>
  <ul><li>Business Transformation</li><li>ERP Implementations</li><li>ERP Solutions</li><li>BI and Data</li><li>Building the Right Team...</li></ul>
</div>
<div class="col" style="left:900px">
  <h4>Contact info</h4>
  <div class="contact-item"><svg width="13" height="10" viewBox="0 0 13 10"><rect width="13" height="10" rx="1" fill="#f0b719"/><path d="M0 1l6.5 4.5L13 1" fill="none" stroke="#46566e" stroke-width="1.2"/></svg>Email:<br>hello@solvanta-mail.com</div>
  <div class="contact-item"><svg width="13" height="13" viewBox="0 0 13 13"><path d="M3 0 5 3 3.5 4.5C4.5 6.5 6.5 8.5 8.5 9.5L10 8l3 2-1.5 2.5C6 12 1 7 .5 1.5z" fill="#f0b719"/></svg>Phone:<br>+44 100 555 0199</div>
  <div class="contact-item"><svg width="11" height="14" viewBox="0 0 11 14"><path d="M5.5 0A5.5 5.5 0 0 0 0 5.5C0 9.5 5.5 14 5.5 14S11 9.5 11 5.5A5.5 5.5 0 0 0 5.5 0z" fill="#f0b719"/><circle cx="5.5" cy="5.5" r="2" fill="#46566e"/></svg>Location:<br>Some address line goes here city name</div>
</div>

<div class="bottom-bar">© Solvanta Design 2023, All Rights Reserved</div>
<div class="chat"><svg width="24" height="22" viewBox="0 0 24 22"><path d="M12 1C5.9 1 1 5 1 10c0 2.6 1.3 4.9 3.4 6.5L3 21l5-2.6c1.2.4 2.6.6 4 .6 6.1 0 11-4 11-9S18.1 1 12 1z" fill="#fff"/></svg></div>

</body>
</html>
```